Beacon Advisory Website

I currently have a website www.beaconadvisoryinc.com. We are a IT Consulting Company. Our website will pretty much tell out our services. I am looking to enhance my website and make it look more professional. Looking for very classy and Contemporary look and design for my website.

It Company

```html
<!DOCTYPE html>
<html lang="en">
<head>
<meta charset="utf-8">
<title>Beacon Advisory</title>
<link href="https://fonts.googleapis.com/css2?family=Open+Sans:ital,wght@0,400;0,600;0,700;1,400&family=Raleway:wght@500;600&family=Ubuntu:wght@400;500;700&display=swap" rel="stylesheet">
<style>
:root{
  --brand:#1b5ea6;
  --brand-dark:#12508f;
  --sky:#0a8ed0;
  --sky-dark:#0979b6;
  --card-active:#0b8bcf;
  --grey-icon:#a8a8a8;
  --text:#555;
  --heading:#555;
  --line:#d6d6d6;
  --white:#fff;
}
*{margin:0;padding:0;box-sizing:border-box}
html,body{width:729px;height:1200px;overflow:hidden;background:var(--white)}
body{position:relative;font-family:"Open Sans",sans-serif;color:var(--text)}
.abs{position:absolute}

/* hero */
.hero{left:0;top:0;width:729px;height:332px;background:linear-gradient(100deg,#c9d3dd 0%,#e7ecf0 30%,#d6dde4 55%,#f0f2f2 75%,#cfd8c4 100%)}
.topline{left:0;top:0;width:729px;height:2px;background:var(--sky)}
.header{left:0;top:2px;width:729px;height:56px;background:rgba(255,255,255,.45)}
.logo{left:80px;top:20px;display:flex;align-items:center;gap:6px;font-family:"Ubuntu",sans-serif;font-weight:700;font-size:15px;color:var(--brand);letter-spacing:.5px}
.logo-mark{width:14px;height:14px;background:var(--brand);border-radius:50%}
.nav{left:297px;top:0;height:58px;display:flex;font-family:"Ubuntu",sans-serif;font-weight:700;font-size:7.5px;color:#333}
.nav a{display:block;height:58px;line-height:62px;text-decoration:none;color:inherit}
.nav .active{background:var(--sky);color:var(--white);width:37px;text-align:center}
.hero-text{left:439px;top:90px;width:209px;height:152px;background:var(--brand);color:var(--white);font-size:7.6px;line-height:15.2px;text-transform:uppercase;text-align:justify;padding:16px 16px 0}
.dot{top:230px;width:6px;height:6px;border-radius:50%;background:rgba(255,255,255,.7)}

/* features */
.feature-photo{top:268px;width:192px;height:101px}
.feature h3{font-family:"Ubuntu",sans-serif;font-weight:400;font-size:13px;color:var(--brand);position:absolute;top:378px;white-space:nowrap}
.feature p{position:absolute;top:401px;width:200px;font-size:7px;line-height:12.5px;color:#555}
.btn{position:absolute;top:435px;width:58px;height:19px;background:var(--brand);color:var(--white);font-size:7.5px;font-weight:700;text-align:center;line-height:19px;border-radius:1px}

/* about */
.about{left:0;top:471px;width:729px;height:149px;background:linear-gradient(90deg,#3e76b4 0%,#4b86c5 45%,#4280c0 75%,#3c73ad 100%)}
.about h2{position:absolute;left:0;top:20px;width:729px;text-align:center;font-family:"Ubuntu",sans-serif;font-weight:500;font-size:12px;color:var(--white);letter-spacing:.3px}
.about p{position:absolute;left:115px;top:48px;width:499px;text-align:center;color:var(--white);font-size:7.1px;line-height:14.5px}
.btn-ghost{position:absolute;left:336px;top:116px;width:58px;height:19px;border:1px solid var(--white);color:var(--white);font-size:7.5px;font-weight:700;text-align:center;line-height:17px}

/* services */
.section-title{left:0;top:640px;width:729px;text-align:center;font-family:"Ubuntu",sans-serif;font-weight:700;font-size:12px;color:var(--brand)}
.card{width:175px;height:167px;border:1px solid var(--line);background:var(--white);text-align:center}
.card.is-active{background:var(--card-active);border-color:var(--card-active);color:var(--white)}
.card .icon{position:absolute;left:61px;top:9px;width:53px;height:53px;border-radius:50%;background:var(--grey-icon);display:flex;align-items:center;justify-content:center}
.card.is-active .icon{background:var(--white)}
.card h4{position:absolute;left:0;top:69px;width:100%;font-family:"Raleway",sans-serif;font-weight:600;font-size:9.4px;color:var(--heading);letter-spacing:.2px}
.card.is-active h4{color:var(--white)}
.card p{position:absolute;left:16px;top:87px;width:143px;font-size:6.9px;line-height:12.4px;color:#777}
.card.is-active p{color:var(--white)}
.card .more{position:absolute;left:0;top:143px;width:100%;font-size:6.8px;font-style:italic;color:#555}
.card.is-active .more{color:var(--white)}
.more svg{vertical-align:middle;margin-left:3px}

/* footer */
.footer{left:0;top:1054px;width:729px;height:120px;background:var(--sky)}
.footer h5{position:absolute;top:24px;font-family:"Raleway",sans-serif;font-weight:500;font-size:10.5px;color:var(--white)}
.footer ul{position:absolute;top:45px;list-style:none;font-size:6.8px;line-height:12.5px;color:var(--white)}
.footer .addr{position:absolute;top:46px;font-size:6.8px;line-height:9.5px;color:var(--white)}
.social{position:absolute;top:44px;width:15px;height:15px;background:#3b6fb0;border:1px solid #5b8fd0}
.bottom{left:0;top:1174px;width:729px;height:26px;background:var(--sky-dark);text-align:center;font-size:5.8px;line-height:26px;color:#cfe6f4}
</style>
</head>
<body>

<div class="abs hero" role="img" aria-label="Photo of business people meeting in a bright modern office"></div>
<div class="abs topline"></div>
<div class="abs header"></div>
<div class="abs logo"><span class="logo-mark"></span>BEACON ADVISORY</div>
<nav class="abs nav">
  <a class="active">HOME</a>
  <a style="margin-left:12px">ABOUT</a>
  <a style="margin-left:22px">SERVICES</a>
  <a style="margin-left:22px">SOLUTION</a>
  <a style="margin-left:24px">RESOURCE</a>
  <a style="margin-left:22px">CARRER</a>
  <a style="margin-left:24px">CONTACT</a>
</nav>
<div class="abs hero-text">Effective integration of information technology into an organization's business processes has become increa singly crucial to prosperity. It includes such items as the systems software, appli­cation software,hardware,networks and databases associated with managing an organization's information.</div>
<div class="abs dot" style="left:347px"></div>
<div class="abs dot" style="left:361px"></div>
<div class="abs dot" style="left:376px"></div>

<section class="feature">
  <div class="abs feature-photo" style="left:62px;background:linear-gradient(135deg,#9fc6e6,#5e8fbd 60%,#3f6a94)" role="img" aria-label="Photo of a woman touching a digital interface"></div>
  <h3 style="left:60px">Consulting</h3>
  <p style="left:61px">Beacon Advisory has certified professional consult­ants to work with you to help increase the business</p>
  <span class="btn" style="left:60px">Read more</span>
</section>
<section class="feature">
  <div class="abs feature-photo" style="left:269px;background:linear-gradient(180deg,#4b4e55,#8e9298 60%,#6d7076)" role="img" aria-label="Photo of a businessman holding a glowing light bulb balloon"></div>
  <h3 style="left:269px">Staff Augmentation</h3>
  <p style="left:270px">For years Beacon Advisory as been offering our cus­tomers the ability to augment their existing staff ...</p>
  <span class="btn" style="left:269px">Read more</span>
</section>
<section class="feature">
  <div class="abs feature-photo" style="left:474px;background:linear-gradient(135deg,#c7d3df,#7e98b4 55%,#5d7894)" role="img" aria-label="Photo of a smiling team in a meeting room"></div>
  <h3 style="left:475px">Offshore</h3>
  <p style="left:475px">Our Offshore development model has a unique distinc­tion of providing efficient software solutions ...</p>
  <span class="btn" style="left:475px">Read more</span>
</section>

<section class="abs about" role="img" aria-label="Faded photo of a team with a world map backdrop">
  <h2>ABOUT BEACON ADVISORY</h2>
  <p>Today's IT market is a dynamic, fast-paced industry, with ever-increasing demands. Meeting these demands for over 25 years, Beacon Advisory maintains a global presence, aggressively recruiting expertly qualified IT and Management Professionals from around the world and cultivating key partnerships with corporations to understand their business models end-to-end, with a goal of delivering exceptional client service and ensuring a consistent delivery of the</p>
  <span class="btn-ghost">Read more</span>
</section>

<h2 class="abs section-title">SERVICE</h2>

<article class="abs card is-active" style="left:84px;top:681px">
  <div class="icon"><svg width="20" height="22" viewBox="0 0 20 22"><g fill="#0b8bcf"><ellipse cx="10" cy="4" rx="9" ry="3.5"/><path d="M1 7c0 2 4 3.5 9 3.5S19 9 19 7v4c0 2-4 3.5-9 3.5S1 13 1 11z"/><path d="M1 14.5c0 2 4 3.5 9 3.5s9-1.5 9-3.5v3.5c0 2-4 3.5-9 3.5S1 20 1 18z"/></g></svg></div>
  <h4>TEKNOLOGY</h4>
  <p>Erat fringilla aenean pulvinar condimentum velit urna, suspendisse vivam us duis gravida lorem. Ornare sit diam mori lobortis. Ut erat fusce tempor turpis.</p>
  <div class="more">Read More<svg width="4" height="6"><path d="M0 0l4 3-4 3z" fill="currentColor"/></svg></div>
</article>
<article class="abs card" style="left:277px;top:681px">
  <div class="icon"><svg width="20" height="20" viewBox="0 0 20 20" fill="none" stroke="#fff" stroke-width="1.4"><path d="M4 15V9a6 6 0 0112 0v6l2 1H2z"/><path d="M8 18a2 2 0 004 0"/></svg></div>
  <h4>BUSINESS</h4>
  <p>Erat fringilla aenean pulvinar condimentum velit urna, suspendisse vivam us duis gravida lorem. Ornare sit diam mori lobortis. Ut erat fusce tempor turpis.</p>
  <div class="more">Read More<svg width="4" height="6"><path d="M0 0l4 3-4 3z" fill="currentColor"/></svg></div>
</article>
<article class="abs card" style="left:470px;top:681px">
  <div class="icon"><svg width="18" height="18" viewBox="0 0 18 18"><g fill="#fff"><circle cx="9" cy="9" r="6"/><rect x="7.5" y="0" width="3" height="18"/><rect x="0" y="7.5" width="18" height="3"/><rect x="7.5" y="0" width="3" height="18" transform="rotate(45 9 9)"/><rect x="7.5" y="0" width="3" height="18" transform="rotate(-45 9 9)"/></g><circle cx="9" cy="9" r="2.4" fill="#a8a8a8"/></svg></div>
  <h4>APPLICATION</h4>
  <p>Erat fringilla aenean pulvinar condimentum velit urna, suspendisse vivam us duis gravida lorem. Ornare sit diam mori lobortis. Ut erat fusce tempor turpis.</p>
  <div class="more">Read More<svg width="4" height="6"><path d="M0 0l4 3-4 3z" fill="currentColor"/></svg></div>
</article>

<article class="abs card" style="left:84px;top:868px">
  <div class="icon"><svg width="16" height="20" viewBox="0 0 16 20" fill="none" stroke="#fff" stroke-width="1.3"><path d="M1 1h9l5 5v13H1z"/><path d="M10 1v5h5M4 10h8M4 13h8M4 16h8"/></svg></div>
  <h4>DEVELOPMENT</h4>
  <p>Erat fringilla aenean pulvinar condimentum velit urna, suspendisse vivam us duis gravida lorem. Ornare sit diam mori lobortis. Ut erat fusce tempor turpis.</p>
  <div class="more">Read More<svg width="4" height="6"><path d="M0 0l4 3-4 3z" fill="currentColor"/></svg></div>
</article>
<article class="abs card" style="left:277px;top:868px">
  <div class="icon"><svg width="22" height="14" viewBox="0 0 22 14"><path d="M5 14a5 5 0 010-10 6 6 0 0111 1 4.5 4.5 0 011 9z" fill="#fff"/></svg></div>
  <h4>ENTERPRISE INTEGRATION</h4>
  <p>Erat fringilla aenean pulvinar condimentum velit urna, suspendisse vivam us duis gravida lorem. Ornare sit diam mori lobortis. Ut erat fusce tempor turpis.</p>
  <div class="more">Read More<svg width="4" height="6"><path d="M0 0l4 3-4 3z" fill="currentColor"/></svg></div>
</article>
<article class="abs card" style="left:470px;top:868px">
  <div class="icon"><svg width="18" height="18" viewBox="0 0 18 18" fill="none" stroke="#fff" stroke-width="1.6"><circle cx="9" cy="9" r="7.5"/><path d="M9 4.5V9H6"/></svg></div>
  <h4>IT CONSULTANCY</h4>
  <p>Erat fringilla aenean pulvinar condimentum velit urna, suspendisse vivam us duis gravida lorem. Ornare sit diam mori lobortis. Ut erat fusce tempor turpis.</p>
  <div class="more">Read More<svg width="4" height="6"><path d="M0 0l4 3-4 3z" fill="currentColor"/></svg></div>
</article>

<footer class="abs footer">
  <h5 style="left:97px">Quick Links</h5>
  <ul style="left:97px"><li>Home</li><li>About Us</li><li>Services</li><li>Solution</li><li>Resources</li><li>Career</li></ul>
  <h5 style="left:250px">Contact Us</h5>
  <div class="addr" style="left:250px">Head Office<br>240 Harbor Lane<br>Suite 205<br>Millbrook, NJ 07099<br>Phone: +1 (555) 014 2288</div>
  <div class="addr" style="left:366px">Technical Center<br>7720 Cedar Ridge Road<br>Suite 255<br>Lakeview MI 48399</div>
  <h5 style="left:554px">Follow Us</h5>
  <span class="social" style="left:556px"></span>
  <span class="social" style="left:576px"></span>
  <span class="social" style="left:596px"></span>
  <span class="social" style="left:616px;background:#eef3f7;border-color:#cfdbe5">
    <svg width="13" height="13" viewBox="0 0 13 13" style="display:block"><rect x="1.5" y="3" width="10" height="7" fill="none" stroke="#9aa8b4" stroke-width="0.9"/><path d="M1.5 3l5 4 5-4" fill="none" stroke="#9aa8b4" stroke-width="0.9"/></svg>
  </span>
</footer>
<div class="abs bottom">© 2015 • www.companyname.com • PRIVACY POLICY</div>

</body>
</html>
```